Online interactive calendar for training organisation

We have a new website being made and need a design for an online calendar that is interactive and very simple and easy to use. On our main page this calendar will include all of our courses (approx 30 different ones with up to 8 different locations). On our sub pages which have course information, the calendar will only include details of that specific course. Details needed are: Course code, course name/title, date, duration (1/2 day - 5 days), location, price, discount price. Maybe also a key for available or limited spots left? We want a section at the top of the calendar to be able to filter by location or course, and maybe to filter by month also? I have included a spreadsheet with a sample of our courses with this information. Also a sample draft of the main page on our new webpage to show the colour green which is our company colour. Main notes - we want as simple, effective and easy to use as possible.
We will need to know what plug in we can use to get the design you have created.

Target Market(s)

Mining and construction - both companies and individuals

Number of Pages Required

1 page

Colors
cadf82

Requirements
Must have
• Be simple, easy to use, effective.

```html
<!DOCTYPE html>
<html lang="en">
<head>
<meta charset="utf-8">
<title>Ridgeline Safety – Training Calendar</title>
<link href="https://fonts.googleapis.com/css2?family=Poppins:wght@400;500;600;700&display=swap" rel="stylesheet">
<style>
:root{
  --green:#cadf82;
  --green-dark:#8fb33a;
  --red:#d8202a;
  --ink:#222;
  --muted:#555;
  --line:#e2e2e2;
  --dark:#2b2b2b;
  --white:#fff;
}
*{box-sizing:border-box;margin:0;padding:0}
html,body{width:1200px;height:2347px;overflow:hidden}
body{position:relative;font-family:'Poppins',sans-serif;color:var(--ink);background:var(--white)}
.abs{position:absolute}

.topbar{left:0;top:0;width:1200px;height:43px;background:var(--green)}
.social{display:flex;gap:4px}
.social span{width:16px;height:16px;border-radius:50%;background:#111;display:block}
.topbar .social{position:absolute;left:111px;top:12px}
.student-btn{position:absolute;left:902px;top:12px;width:79px;height:19px;background:#222;color:#fff;font-size:8px;font-weight:600;border-radius:2px;text-align:center;line-height:19px}
.search{position:absolute;left:987px;top:12px;width:100px;height:19px;background:#fff;border-radius:2px}
.search svg{position:absolute;right:7px;top:5px}

.header{left:0;top:43px;width:1200px;height:103px;background:#fff}
.brand{position:absolute;left:112px;top:26px;display:flex;align-items:center;gap:10px}
.brand-mark{width:44px;height:44px;border-radius:50%;background:var(--red)}
.brand-name{font-size:22px;font-weight:700;color:var(--red);line-height:1;white-space:nowrap}
.brand-tag{font-size:10px;font-weight:500;color:#333;margin-top:4px;letter-spacing:.5px}
.nav{position:absolute;right:112px;top:30px;display:flex;gap:12px;font-size:16px}
.nav a{color:#222;text-decoration:none;padding:6px 8px;border-radius:3px}
.nav a.active{background:var(--green)}

.hero{left:0;top:146px;width:1200px;height:514px;background:linear-gradient(120deg,#6e6a66,#a39b8f 45%,#c7b994 65%,#55708d)}
.hero h1{position:absolute;top:146px;width:1200px;text-align:center;color:#fff;font-size:46px;font-weight:600;line-height:58px}
.hero h1 span{font-weight:400;display:block}

.card{background:#fff;border-radius:34px;box-shadow:0 4px 18px rgba(0,0,0,.12);overflow:hidden}
.card-head{height:79px;background:var(--green);color:#fff;font-weight:700;font-size:30px;text-align:center;line-height:79px}
.difference{left:112px;top:518px;width:976px;height:624px}
.lead{text-align:center;font-size:17px;color:#333;margin-top:26px}
.tiles{position:absolute;left:14px;top:165px;display:grid;grid-template-columns:repeat(5,185px);gap:11px 6px}
.tile{height:205px;border:2px solid var(--line);border-top:none;background:#fff}
.tile .photo{height:146px}
.tile p{height:57px;display:flex;align-items:center;justify-content:center;text-align:center;font-size:17px;font-weight:600;line-height:19px;padding:0 10px}

.calendar{left:112px;top:1201px;width:976px;height:435px}
.filters{position:absolute;left:19px;top:113px;display:flex;gap:13px}
.filter{width:304px;height:60px;border:2px solid var(--line);padding:0 14px;display:flex;align-items:center;justify-content:space-between}
.filter b{font-size:17px;font-weight:500;display:block;line-height:20px}
.filter small{font-size:13px;color:#333}
.events{position:absolute;left:14px;top:199px;display:flex;gap:7px}
.event{border:2px solid var(--line);height:194px;padding:18px 4px 0 8px;overflow:hidden}
.event dl{display:grid;grid-template-columns:auto auto;column-gap:10px;row-gap:6.5px;font-size:12.5px;line-height:17px;white-space:nowrap}
.event dt{text-align:right;color:#333;font-weight:500}
.event dd{color:#555}

.banner{left:0;top:1720px;width:1200px;height:407px;background:linear-gradient(90deg,#7a7a6c,#a39a6c 30%,#c9c9c2 55%,#dedede)}
.banner-photo{position:absolute;left:0;top:0;width:620px;height:407px;background:linear-gradient(160deg,#c8c9c7,#b89a3c 45%,#6d6757)}
.banner-frame{position:absolute;left:764px;top:68px;width:244px;height:272px;border:12px solid #fff;opacity:.9}
.banner-text{position:absolute;left:625px;top:155px;width:380px;font-weight:700;font-size:33px;line-height:42px;color:#2c2c2c;text-align:center;white-space:nowrap}
.banner-pill{position:absolute;left:651px;top:258px;width:329px;height:22px;background:var(--green-dark);color:#fff;font-size:9px;text-align:center;line-height:22px;white-space:nowrap;overflow:hidden}

.footer{left:0;top:2127px;width:1200px;height:180px;background:var(--dark);color:#ddd}
.footer .brand{left:224px;top:50px}
.footer .brand-mark{width:38px;height:38px}
.footer .brand-name{font-size:20px}
.follow{position:absolute;left:267px;top:108px;display:flex;gap:8px;align-items:center;font-size:12px}
.follow .social span{border-radius:2px;background:#111;width:18px;height:18px}
.fnav{position:absolute;left:618px;top:71px;display:flex;gap:18px;font-size:9px}
.fcontact{position:absolute;left:588px;top:106px;display:flex;gap:22px;font-size:11px;align-items:center}
.fcontact div{display:flex;align-items:center;gap:10px}
.fcontact i{width:22px;height:22px;background:#111;display:flex;align-items:center;justify-content:center}
.to-top{position:absolute;left:1010px;top:156px;width:36px;height:36px;background:#fff;border:1px solid #ccc;display:flex;align-items:center;justify-content:center}
.copybar{left:0;top:2307px;width:1200px;height:40px;background:var(--green);text-align:center;font-size:9px;line-height:40px;color:#333}
</style>
</head>
<body>

<div class="abs topbar">
  <div class="social"><span></span><span></span><span></span><span></span></div>
  <div class="student-btn">Student Access</div>
  <div class="search"><svg width="9" height="9" viewBox="0 0 10 10"><circle cx="4" cy="4" r="3" fill="none" stroke="#222" stroke-width="1.6"/><line x1="6.2" y1="6.2" x2="9" y2="9" stroke="#222" stroke-width="1.6"/></svg></div>
</div>

<div class="abs header">
  <div class="brand">
    <div class="brand-mark"></div>
    <div><div class="brand-name">RIDGELINE SAFETY</div><div class="brand-tag">SAFETY AND TRAINING</div></div>
  </div>
  <nav class="nav">
    <a class="active">Home</a><a>Courses</a><a>About Us</a><a>Funding</a><a>Location</a><a>Contact Us</a>
  </nav>
</div>

<div class="abs hero" role="img" aria-label="Photo of construction workers in hard hats and hi-vis vests">
  <h1>Training a Safety Culture<span>That Counts</span></h1>
</div>

<section class="abs card difference">
  <div class="card-head">THE RIDGELINE SAFETY DIFFERENCE</div>
  <p class="lead">Commited To Helping Our Students Succeed.</p>
  <div class="tiles">
    <div class="tile"><div class="photo" role="img" aria-label="Loader at a quarry" style="background:linear-gradient(135deg,#8a8a84,#c79a3a)"></div><p>All Courses</p></div>
    <div class="tile"><div class="photo" role="img" aria-label="Gloved handshake" style="background:linear-gradient(135deg,#4aa3df,#e6c13a)"></div><p>Funded Courses</p></div>
    <div class="tile"><div class="photo" role="img" aria-label="Red mining truck" style="background:linear-gradient(135deg,#9a9a96,#c9363a)"></div><p>Mining</p></div>
    <div class="tile"><div class="photo" role="img" aria-label="Excavator on rocky ground" style="background:linear-gradient(135deg,#6f6d66,#c49b2c)"></div><p>Standard 11</p></div>
    <div class="tile"><div class="photo" role="img" aria-label="Workers on a rooftop" style="background:linear-gradient(135deg,#8fa06a,#5a5f66)"></div><p>Work Safety At Heights</p></div>
    <div class="tile"><div class="photo" role="img" aria-label="Business meeting at a laptop" style="background:linear-gradient(135deg,#3b3f46,#b9b4ad)"></div><p>Corporate Clients</p></div>
    <div class="tile"><div class="photo" role="img" aria-label="Group studying online" style="background:linear-gradient(135deg,#d9b77a,#4e9ac0)"></div><p>Online Courses</p></div>
    <div class="tile"><div class="photo" role="img" aria-label="Engineers reviewing plans on site" style="background:linear-gradient(135deg,#4f8fd1,#c8b868)"></div><p>RPL’s &amp; VOC’s</p></div>
    <div class="tile"><div class="photo" role="img" aria-label="Worker beside yellow elevated platform" style="background:linear-gradient(135deg,#7a7d80,#d8c33a)"></div><p>Plant &amp; Equipment</p></div>
    <div class="tile"><div class="photo" role="img" aria-label="Construction worker on a concrete site" style="background:linear-gradient(135deg,#b5a085,#d27a2c)"></div><p>Construction</p></div>
  </div>
</section>

<section class="abs card calendar">
  <div class="card-head">CALENDAR</div>
  <div class="filters">
    <div class="filter"><div><b>LOCATION</b><small>Townsville</small></div><svg width="16" height="10" viewBox="0 0 16 10"><path d="M2 2l6 6 6-6" fill="none" stroke="#222" stroke-width="3"/></svg></div>
    <div class="filter"><b>COURSE</b><svg width="16" height="10" viewBox="0 0 16 10"><path d="M2 2l6 6 6-6" fill="none" stroke="#222" stroke-width="3"/></svg></div>
    <div class="filter"><b>MONTH</b><svg width="16" height="10" viewBox="0 0 16 10"><path d="M2 2l6 6 6-6" fill="none" stroke="#222" stroke-width="3"/></svg></div>
  </div>
  <div class="events">
    <div class="event" style="width:300px"><dl>
      <dt>Course code:</dt><dd>TLIL0005 Basic Scaffolding</dd><dt>Time:</dt><dd>8 am</dd><dt>Date:</dt><dd>Mon, November, 04, 2019</dd><dt>Duration:</dt><dd>5 days</dd><dt>Location:</dt><dd>Townsville</dd><dt>Price:</dt><dd>$ 500.00</dd><dt>Discount Price:</dt><dd>$200.00</dd></dl></div>
    <div class="event" style="width:300px"><dl>
      <dt>Course code:</dt><dd>CPR Refresher</dd><dt>Time:</dt><dd>8 am</dd><dt>Date:</dt><dd>Wed, November, 04, 2019</dd><dt>Duration:</dt><dd>½ day</dd><dt>Location:</dt><dd>Townsville</dd><dt>Price:</dt><dd>$ 150.00</dd><dt>Discount Price:</dt><dd>$80.00</dd></dl></div>
    <div class="event" style="width:335px"><dl>
      <dt>Course code:</dt><dd>TLILIC003 Vehicle Loading crane</dd><dt>Time:</dt><dd>8 am</dd><dt>Date:</dt><dd>Fri, December, 006, 2019</dd><dt>Duration:</dt><dd>5 days</dd><dt>Location:</dt><dd>Townsville</dd><dt>Price:</dt><dd>$ 550.00</dd><dt>Discount Price:</dt><dd>$130.00</dd></dl></div>
  </div>
</section>

<section class="abs banner">
  <div class="banner-photo" role="img" aria-label="Large yellow haul truck at a mine site"></div>
  <div class="banner-frame"></div>
  <div class="banner-text">Training a Safety<br>Culture that Counts</div>
  <div class="banner-pill">NOW TRAINING - Working at Heights &amp; Confined Spaces courses</div>
</section>

<footer class="abs footer">
  <div class="brand abs">
    <div class="brand-mark"></div>
    <div class="brand-name">RIDGELINE SAFETY</div>
  </div>
  <div class="follow">Follow us on :- <div class="social"><span></span><span></span><span></span><span></span></div></div>
  <div class="fnav"><span>Home</span><span>Courses</span><span>Our Services</span><span>About us</span><span>Funding</span><span>Locations</span><span>Contact us</span></div>
  <div class="fcontact">
    <div><i><svg width="9" height="12" viewBox="0 0 9 12"><path d="M4.5 0a4.5 4.5 0 0 0-4.5 4.5C0 8 4.5 12 4.5 12S9 8 9 4.5A4.5 4.5 0 0 0 4.5 0z" fill="#fff"/><circle cx="4.5" cy="4.5" r="1.6" fill="#111"/></svg></i>18 Harbour Lane, Brookvale QLD 4000</div>
    <div><i><svg width="12" height="9" viewBox="0 0 12 9"><rect width="12" height="9" fill="#fff"/><path d="M0 0l6 5 6-5" fill="none" stroke="#111" stroke-width="1.2"/></svg></i>info@ridgelinesafety.edu.au</div>
  </div>
  <div class="to-top"><svg width="14" height="9" viewBox="0 0 14 9"><path d="M1 8l6-6 6 6" fill="none" stroke="#222" stroke-width="2"/></svg></div>
</footer>
<div class="abs copybar">© Copyright All Right Reserved | Powered by Ridgeline Safety.</div>

</body>
</html>
```